Corporate Values project needs own identity (logo, illustrations, font)

For a project to liven up corporate values we have designed 10 questions our employees should ask themselves at any time. To start marketing these, we want to have various outings (posters, cards, leaflets, etc) that illustrate these questions. preferably with a logo / font of its own. Look and feel / moodwords: insurance, blue, values, non negociable, fun, vintage, together. The 10 questions are:
1. What would the customer say?
2. How will this help those of us in front of the customer?
3. Have I expressed my views clearly and openly?
4. How can we do this differently and to higher standards? Better, faster, simpler?
5. How can I help, beyond my specific role description?
6. Have I recognised other people’s contributions and ideas?
7. Am I keeping my commitments to others, internal or externally?
8. How can I learn more? And how can I share more so others can learn form this?
9. Who needs, and who does not need to be involved?
10. Is there a different or alternative view, opinion or option?

Preferably, each question gets its own little ilustration.

If things are not clear, or more information needed, please let me know.

Reason: Since part of the project has been postponed, we can take more time for the design.

```html
<!DOCTYPE html>
<html lang="en">
<head>
<meta charset="utf-8">
<title>Question 4 of 10 – How can I learn more?</title>
<link rel="stylesheet" href="https://fonts.googleapis.com/css2?family=Bebas+Neue&family=Oswald:wght@200&display=swap">
<style>
  :root {
    --teal: #00b3b4;
    --cyan: #00ffff;
    --track: #00d2d3;
    --white: #ffffff;
    --illustration-tone: rgba(0, 255, 255, 0.16);
  }
  html, body {
    margin: 0;
    padding: 0;
    overflow: hidden;
  }
  .card {
    position: relative;
    width: 1200px;
    height: 1000px;
    background: var(--teal);
    overflow: hidden;
  }
  .progress {
    position: absolute;
    left: 37px;
    top: 37px;
    width: 808px;
    height: 6px;
    background: var(--track);
  }
  .progress__fill {
    width: 323px;
    height: 100%;
    background: var(--cyan);
  }
  .step {
    position: absolute;
    left: 38px;
    top: 82px;
    margin: 0;
    font-family: "Bebas Neue", "Arial Narrow", sans-serif;
    font-size: 53px;
    line-height: 1;
    color: var(--cyan);
    letter-spacing: 1.5px;
  }
  .question {
    position: absolute;
    left: 38px;
    top: 189px;
    margin: 0;
    font-family: "Bebas Neue", "Arial Narrow", sans-serif;
    font-weight: 400;
    font-size: 148px;
    line-height: 1;
    color: var(--white);
    letter-spacing: 0;
    white-space: nowrap;
  }
  .follow-up {
    position: absolute;
    left: 40px;
    top: 318px;
    margin: 0;
    font-family: "Oswald", "Arial Narrow", sans-serif;
    font-weight: 200;
    font-size: 92px;
    line-height: 102px;
    color: var(--white);
    text-transform: uppercase;
    letter-spacing: 0;
    white-space: nowrap;
    transform: scaleX(0.93);
    transform-origin: left top;
  }
  .illustration {
    position: absolute;
    left: 30px;
    top: 628px;
    width: 792px;
    height: 282px;
    background: var(--illustration-tone);
    border-radius: 6px;
  }
</style>
</head>
<body>
  <main class="card">
    <div class="progress" aria-hidden="true"><div class="progress__fill"></div></div>
    <p class="step">4/10</p>
    <h1 class="question">How can I learn more?</h1>
    <p class="follow-up">And how can I share more<br>so others can learn from this?</p>
    <div class="illustration" role="img" aria-label="Line illustration: a person with a light bulb idea, arrows spreading it to a group of three people who each gain a light bulb"></div>
  </main>
</body>
</html>
```